Black Car Limousine transportation business in Naples Florida

Always stand for my reliability and RVD stands for Love, K and M are the first initials of my children's names. It should show professionalism and a dedication to customer service. We keep our clients identities private. Show our professionalism. We are Black car Black tie company. We service transportation on a reserve basis to and from residents, airports, casinos, hotels,

Target Market(s)

It is a Private car service. High end clients. Businesses, Celebrity and athletes. Service to airports, hotels, special events.

Industry/Entity Type

Business

Contact Information for Business Card

A pearl metallic or Luster card. Standard business card size. Would like the name, Company email, show we take credit cards and phone number. Currently I don't have a website but will like to add later.

Logo Text

STEADFAST RVD TRANSPORTATION

Font styles to use
Serif

Colors
eaeaea
000000

Requirements
Must have
• Must have Company email, show we take credit cards and phone number. Currently I don't have a website but will like to add later.
Nice to have
• Would like to stay with a black and white theme. Open to some color trim.
Should not have
• Open to suggestions

```html
<!DOCTYPE html>
<html lang="en">
<head>
<meta charset="utf-8">
<title>Steadfast RVD Transportation – Business Card</title>
<link href="https://fonts.googleapis.com/css2?family=Source+Serif+4:opsz,wght@8..60,400;8..60,600;8..60,700&display=swap" rel="stylesheet">
<style>
  :root {
    --backdrop: #9c9c9c;
    --card-light: #ffffff;
    --card-dark: #333333;
    --ink: #2b2b2b;
    --ink-soft: #3a3a3a;
    --paper-text: #ffffff;
    --icon-line: #2b2b2b;
  }
  * { margin: 0; padding: 0; box-sizing: border-box; }
  html, body { width: 1200px; height: 900px; overflow: hidden; }
  body {
    background: var(--backdrop);
    font-family: "Source Serif 4", Georgia, "Times New Roman", serif;
    position: relative;
  }
  .card {
    position: absolute;
    top: 170px;
    width: 347px;
    height: 561px;
  }
  .card--front { left: 259px; background: var(--card-light); color: var(--ink); }
  .card--back { left: 631px; background: var(--card-dark); color: var(--paper-text); }

  .tab {
    position: absolute;
    left: 102px;
    width: 143px;
    background: var(--card-dark);
  }
  .tab--top { top: 0; height: 31px; }
  .tab--bottom { bottom: 0; height: 28px; }

  .brand {
    position: absolute;
    top: 142px;
    left: 0;
    width: 100%;
    text-align: center;
    font-weight: 700;
    line-height: 1;
  }
  .brand__lead { font-size: 14px; letter-spacing: 5px; }
  .brand__mark { font-size: 72px; letter-spacing: 3px; margin-top: 2px; }
  .brand__tail { font-size: 22px; letter-spacing: 1px; margin-top: 4px; }

  .contact {
    position: absolute;
    top: 330px;
    left: 0;
    width: 100%;
    text-align: center;
    color: var(--ink-soft);
  }
  .contact__name { font-size: 21px; font-weight: 600; color: var(--ink); line-height: 1; letter-spacing: 0.5px; }
  .contact__role { font-size: 14px; margin-top: 7px; }
  .contact__lines { list-style: none; margin-top: 16px; font-size: 14px; line-height: 21px; }
  .contact__lines b { font-weight: 700; }

  .payments {
    display: flex;
    justify-content: center;
    align-items: center;
    gap: 6px;
    margin-top: 7px;
    font-size: 12px;
    line-height: 1;
  }
  .payments__icons { display: flex; gap: 4px; }
  .payments__icon { width: 22px; height: 15px; display: block; }

  .contact__address { font-size: 14px; line-height: 17px; margin-top: 12px; }

  .vehicle {
    position: absolute;
    left: 24px;
    top: 365px;
    width: 307px;
    height: 173px;
    border-radius: 30px 50px 10px 10px;
    background: radial-gradient(ellipse at 50% 50%, #1a1a1a 0%, #111111 55%, #2c2c2c 100%);
  }
</style>
</head>
<body>
  <section class="card card--front">
    <div class="tab tab--top"></div>
    <div class="brand">
      <div class="brand__lead">STEADFAST</div>
      <div class="brand__mark">RVD</div>
      <div class="brand__tail">TRANSPORTATION</div>
    </div>
    <div class="contact">
      <p class="contact__name">DANIEL REYES</p>
      <p class="contact__role">Managing Director</p>
      <ul class="contact__lines">
        <li><b>P:</b> 239-555-0148</li>
        <li><b>E:</b> book@rvdride.com</li>
      </ul>
      <div class="payments">
        <span class="payments__icons" aria-hidden="true">
          <svg class="payments__icon" viewBox="0 0 22 15"><rect x="0.75" y="0.75" width="20.5" height="13.5" rx="2" fill="none" stroke="var(--icon-line)" stroke-width="1.5"/><rect x="0.75" y="3.5" width="20.5" height="2.5" fill="var(--icon-line)"/></svg>
          <svg class="payments__icon" viewBox="0 0 22 15"><rect x="0.75" y="0.75" width="20.5" height="13.5" rx="2" fill="none" stroke="var(--icon-line)" stroke-width="1.5"/><rect x="3.5" y="5" width="5" height="4" rx="0.8" fill="var(--icon-line)"/></svg>
          <svg class="payments__icon" viewBox="0 0 22 15"><rect x="0.75" y="0.75" width="20.5" height="13.5" rx="2" fill="none" stroke="var(--icon-line)" stroke-width="1.5"/><rect x="3.5" y="9.5" width="15" height="1.5" fill="var(--icon-line)"/></svg>
        </span>
        <span>Major credit cards accepted</span>
      </div>
      <p class="contact__address">4510 Harbor Lane Naples<br>Florida, 34102</p>
    </div>
    <div class="tab tab--bottom"></div>
  </section>

  <section class="card card--back">
    <div class="brand">
      <div class="brand__lead">STEADFAST</div>
      <div class="brand__mark">RVD</div>
      <div class="brand__tail">TRANSPORTATION</div>
    </div>
    <div class="vehicle" role="img" aria-label="Photo of a black luxury SUV"></div>
  </section>
</body>
</html>
```